International online gaming platform needs a game UI design

1. We need a game interface for three kinds of theme based on our guideline and sample mockup.
2. The product type is the online casino games related, we need a series of casino games UIs, however, we can start on the game lobby first.
3. Three theme you might choose from or refer to:
A. 3D look & feel
B. Realistic casino theme
C. Richness and grandeur
D. European casino style
4. NOT ALLOWED to change the design layout.
MUST follow our sample mock up and ONLY redefine the design style.
5. All items must be in a stand-alone component, eg. Button, Tab, Icon,... etc.
6. We need the layout in vector shape, but we can review in JPG or PNG format.
7. The image size: 1366 x 768

Updated:
1. All items and their positions should be same as the sample UI we provided.
Please redesign all the items and create a new theme for it.
No need to create a new layout.
2. Although we accept the draft design, but all the items in UI should be completed.
3. All the wordings in the sample UI are confirmed, you might change the fonts.
4. For the avatar in the left hand side, you don't have to redraw it.
We already have our own avatar system implemented.
5. All the items such as icons, tabs, and buttons are free to redesign.

Dear designers,

We've increased our budget and raise the prize money to 800 USD.  
We also accept the draft design in PNG format and we can go through the details in handover stage.
Thank you very much. 

Reason: Dear designers, We decided to extend the deadline by 7 days. As mentioned in the task description, we are looking for a new style of design and you might refer to the below style. A. 3D look & feel B. Realistic casino theme C. Richness and grandeur D. European casino style If you are still interested in our project, please send us your work. Thank you very much!

```html
<!DOCTYPE html>
<html lang="en">
<head>
<meta charset="utf-8">
<title>Live Casino Lobby</title>
<link rel="stylesheet" href="https://fonts.googleapis.com/css2?family=Open+Sans:wght@400;600;700&display=swap">
<style>
:root{
  --bg-deep:#170820;
  --bg-mid:#3b1650;
  --bg-glow:#b0439f;
  --panel:#07070a;
  --panel-edge:#2a63c8;
  --silver-hi:#ffffff;
  --silver:#c9ccd3;
  --silver-dark:#5c6068;
  --blue:#1e5fc4;
  --blue-deep:#0f2f78;
  --blue-light:#5aa4ff;
  --green:#2f8a1e;
  --green-deep:#1b5710;
  --green-light:#9be35c;
  --gold:#e8b923;
  --gold-light:#fff0a0;
  --gold-dark:#8a5e04;
  --yellow-text:#f4e03a;
  --white:#ffffff;
  --grid-line:#b8cde8;
  --red:#d8261e;
}
*{box-sizing:border-box;margin:0;padding:0}
html,body{width:1200px;height:675px;overflow:hidden;background:var(--bg-deep)}
body{font-family:"Open Sans",Arial,sans-serif;color:var(--white)}
.stage{position:absolute;left:0;top:0;width:1366px;height:768px;transform:scale(0.87848);transform-origin:0 0;overflow:hidden;
  background:
    radial-gradient(ellipse at 70% 20%,rgba(200,90,220,.35) 0%,rgba(0,0,0,0) 40%),
    radial-gradient(ellipse at 55% 55%,#6e2c84 0%,var(--bg-mid) 45%,var(--bg-deep) 90%)}
.abs{position:absolute}
.sprites{position:absolute;width:0;height:0}
.backdrop{left:470px;top:240px;width:560px;height:528px;border-radius:48% 48% 0 0;
  background:radial-gradient(ellipse at 50% 45%,#ef8fd6 0%,var(--bg-glow) 35%,rgba(90,30,110,0) 75%);opacity:.8}

/* shared gloss */
.gloss{position:absolute;overflow:hidden}
.gloss::after{content:"";position:absolute;left:0;right:0;top:0;height:50%;
  background:linear-gradient(rgba(255,255,255,.45),rgba(255,255,255,.08));border-radius:inherit;pointer-events:none}

/* header */
.brand{left:5px;top:5px;width:383px;height:37px;background:linear-gradient(#1c1c1c,#000);
  border:2px solid var(--silver);box-shadow:inset 0 0 0 1px #000,0 2px 4px #000;
  display:flex;align-items:center;gap:12px;padding-left:12px}
.brand-dot{width:20px;height:20px;border-radius:50%;background:var(--gold)}
.brand-name{font-weight:700;font-size:25px;color:var(--white)}
.clock{left:18px;top:48px;width:190px;height:32px;background:linear-gradient(#222,#050505);border:2px solid #666;border-radius:8px;
  box-shadow:inset 0 1px 0 #888,0 2px 3px #000;
  font-size:11px;display:flex;align-items:center;justify-content:center;color:#eee}

.tools{left:1142px;top:6px;display:flex;gap:8px}
.tool{position:relative;width:37px;height:37px;border-radius:5px;border:2px solid #e6f0ff;
  background:linear-gradient(#6fb0ff,#2568d8 50%,#0f3e9e);box-shadow:0 2px 3px #000;
  display:flex;align-items:center;justify-content:center;overflow:hidden}
.tool::after{content:"";position:absolute;left:0;right:0;top:0;height:48%;background:linear-gradient(rgba(255,255,255,.5),rgba(255,255,255,.1))}
.tool.close{background:linear-gradient(#ff8a7e,var(--red) 50%,#8e120c);border-color:#ffd8d4}

.tab{top:52px;width:260px;height:44px;border-radius:22px;border:3px solid var(--silver);
  box-shadow:0 0 0 2px #1b1b1b,0 3px 6px #000,inset 0 -3px 5px rgba(0,0,0,.35);
  display:flex;align-items:center;justify-content:center;font-weight:700;font-size:21px;padding-left:40px;overflow:visible}
.tab::after{left:14px;right:14px;top:2px;height:45%;border-radius:18px 18px 8px 8px}
.tab span{position:relative;z-index:1;text-shadow:0 1px 2px rgba(0,0,0,.6)}
.tab.blue{background:linear-gradient(#7aa6f0,#2d58b4 48%,#1a357c 52%,#223f8e)}
.tab.green{background:linear-gradient(#a6e46a,#3e9a24 48%,#226c14 52%,#2e7d1c)}
.tab-icon{position:absolute;left:-10px;top:-6px;z-index:2}

/* profile */
.side-panel{background:linear-gradient(#111,var(--panel));border:3px solid var(--panel-edge);border-radius:8px;
  box-shadow:0 0 0 2px #0b1a3a,0 0 10px rgba(60,120,255,.35)}
.profile{left:15px;top:92px;width:195px;height:308px}
.avatar{left:25px;top:108px;width:170px;height:204px;background:linear-gradient(#474747,#161616);border:3px solid #8a8a8a;box-shadow:inset 0 0 8px #000}
.player-name{left:25px;top:314px;width:170px;height:28px;background:linear-gradient(#a5a5a5,#5a5a5a 50%,#3d3d3d);font-size:16px;display:flex;align-items:center;justify-content:center}
.profile-btn{left:25px;top:348px;width:170px;height:38px;background:linear-gradient(#6aa4ff,var(--blue) 50%,#1548a6);border-radius:3px;
  display:flex;align-items:center;gap:20px;padding-left:6px;font-size:17px}
.icon-box{position:relative;z-index:1;width:28px;height:28px;background:#111;border:1px solid #ddd;border-radius:3px;display:flex;align-items:center;justify-content:center}
.menu{left:15px;top:420px;width:195px;height:290px}
.menu-btn{left:22px;width:170px;height:38px;border-radius:8px;border:2px solid #9fb6e8;
  background:linear-gradient(#4f82de,#1f48a6 50%,#122d70);box-shadow:0 2px 4px #000;
  display:flex;align-items:center;gap:12px;padding-left:4px;font-size:12.5px}
.menu-btn span.lbl,.profile-btn span.lbl{position:relative;z-index:1}

/* dealers */
.dealer-frame{background:linear-gradient(#ffffff,#b7b9bf 40%,#6e7076);padding:4px;border-radius:2px;box-shadow:0 2px 5px #000}
.dealer-inner{width:100%;height:100%;background:linear-gradient(#1a1a1a,#050505);position:relative}
.score-grid{position:absolute;background-color:#fff;
  background-image:linear-gradient(var(--grid-line) 1px,transparent 1px),linear-gradient(90deg,var(--grid-line) 1px,transparent 1px);
  background-size:14px 13px}
.dealer-photo{position:absolute;border:3px solid var(--blue-light);border-radius:8px;background:linear-gradient(#3478aa,#0b2238);box-shadow:0 0 6px rgba(90,164,255,.6)}
.dealer-bar{position:absolute;background:#000;display:flex;justify-content:space-between;align-items:center;font-size:10px}
.dealer-bar .deals{background:linear-gradient(#3a7ae0,var(--blue-deep));height:100%;padding:0 8px;display:flex;align-items:center}
.dealer-group{left:566px;top:108px;width:782px;height:138px;background:linear-gradient(#ffffff,#b2b4ba 40%,#74767c);padding:4px;box-shadow:0 3px 6px #000}
.dealer-group-inner{width:100%;height:100%;background:#0b0b0b;position:relative}

/* filter bar */
.filter-bar{left:232px;top:263px;width:1118px;height:39px;background:linear-gradient(#2a2a2a,#050505);border-radius:6px;border:1px solid #555;box-shadow:0 2px 5px #000}
.chip{top:267px;height:31px;background:linear-gradient(#ffffff,#d2d2d2 48%,#a3a3a3 52%,#bdbdbd);border-radius:4px;color:#111;font-size:12px;
  display:flex;align-items:center;justify-content:center;gap:6px;box-shadow:inset 0 -1px 0 #777,0 1px 2px #000}
.chip.search{background:linear-gradient(#c2c2c2,#e4e4e4);box-shadow:inset 0 2px 3px #666}

/* tables */
.table-card{width:320px;height:160px;background:linear-gradient(#141414,#020202);border:3px solid var(--silver);border-radius:6px;
  box-shadow:0 0 0 1px #444,0 4px 8px rgba(0,0,0,.8),inset 0 0 0 1px #000}
.t-title,.t-comm{top:6px;font-size:12.5px;color:var(--yellow-text)}
.t-title,.t-limit{left:12px}
.t-comm,.t-count{right:12px}
.t-limit,.t-count{top:22px;font-size:12.5px}
.coin{left:110px;top:12px;width:94px;height:56px;border-radius:50%;
  background:radial-gradient(ellipse at 38% 30%,var(--gold-light) 0%,#f6d24a 30%,var(--gold) 58%,var(--gold-dark) 100%);
  border:2px solid #fff3b0;box-shadow:0 0 0 2px #a67a10,0 3px 5px #000;
  display:flex;align-items:center;justify-content:center;font-size:14px;color:#7a4e00;font-style:italic;z-index:1}
.felt{left:8px;top:62px}
.seats{left:6px;top:124px;display:flex;gap:4px}
.seat{position:relative;width:41px;height:29px;border:1px solid #cde;border-radius:2px;background:linear-gradient(#5ad06a,#1f8a3a 50%,#0d5a22);
  display:flex;align-items:center;justify-content:center;overflow:hidden}
.seat::after{content:"";position:absolute;left:0;right:0;top:0;height:45%;background:linear-gradient(rgba(255,255,255,.35),rgba(255,255,255,.05))}
.seat.open{background:linear-gradient(#ffe07a,#d6a021 50%,#946406)}

.scroll-track{left:1333px;top:342px;width:12px;height:352px;background:#050505;border-radius:3px;box-shadow:inset 0 0 3px #444}
.scroll-thumb{left:1329px;top:355px;width:20px;height:32px;border-radius:4px;background:linear-gradient(#fff,#cfcfcf 48%,#7a7a7a 52%,#aaa);box-shadow:0 1px 3px #000}

.balance{left:1070px;top:728px;width:285px;height:37px;background:linear-gradient(#2c2c2c,#050505);border:2px solid #777;border-radius:10px 0 0 10px;display:flex;align-items:center;box-shadow:0 -1px 4px #000}
.balance-label{width:98px;text-align:center;font-size:16px}
.currency{background:linear-gradient(#ffe07a,var(--gold) 50%,#a97a08);color:#111;font-size:11px;height:100%;padding:0 6px;display:flex;align-items:center}
.balance-value{flex:1;text-align:center;font-size:16px}
</style>
</head>
<body>
<svg class="sprites" aria-hidden="true">
  <defs>
    <linearGradient id="feltFill" x1="0" y1="0" x2="0" y2="1"><stop offset="0" stop-color="#10260a"/><stop offset=".55" stop-color="#3c8a1e"/><stop offset="1" stop-color="#8fe04c"/></linearGradient>
    <symbol id="felt" viewBox="0 0 300 60">
      <path d="M22 2H278L298 58H2Z" fill="url(#feltFill)" stroke="#fff" stroke-width="1.2"/>
      <path d="M12 30H288M59 2L45 58M96 2L88 58M133 2L130 58M170 2L172 58M207 2L215 58M244 2L257 58" stroke="#fff" stroke-width="1"/>
      <g font-family="Open Sans,sans-serif" font-size="11" font-weight="700" font-style="italic" text-anchor="middle">
        <g fill="#f4e03a"><text x="40" y="21">B</text><text x="78" y="21">B</text><text x="115" y="21">B</text><text x="151" y="21">B</text><text x="188" y="21">B</text><text x="225" y="21">B</text><text x="262" y="21">B</text></g>
        <g fill="#fff"><text x="30" y="49">P</text><text x="70" y="49">P</text><text x="110" y="49">P</text><text x="151" y="49">P</text><text x="192" y="49">P</text><text x="233" y="49">P</text><text x="273" y="49">P</text></g>
      </g>
    </symbol>
    <symbol id="person" viewBox="0 0 20 20"><circle cx="10" cy="6" r="5" fill="#ffe2b8"/><path d="M1 20c0-9 18-9 18 0z" fill="#f6b35c"/></symbol>
    <symbol id="drop" viewBox="0 0 22 16"><path d="M1 1h20L11 15z" fill="#ffe68a" stroke="#7a5200" stroke-width="1.5"/></symbol>
  </defs>
</svg>

<div class="stage">
  <div class="abs backdrop" role="img" aria-label="Fantasy character illustration in pink and violet tones"></div>

  <div class="abs brand"><span class="brand-dot"></span><span class="brand-name">LIVE CASINO</span></div>
  <div class="abs clock">12/03/2014&nbsp;&nbsp;09 : 18 AM</div>

  <div class="abs tools">
    <div class="tool"><svg width="22" height="22" viewBox="0 0 22 22"><circle cx="12" cy="9" r="6" fill="none" stroke="#fff" stroke-width="2.5"/><path d="M7 14 L2 20" stroke="#fff" stroke-width="3"/></svg></div>
    <div class="tool"><svg width="22" height="22" viewBox="0 0 22 22"><circle cx="11" cy="11" r="8" fill="none" stroke="#fff" stroke-width="2.5"/><text x="11" y="15.5" font-size="12" font-weight="700" fill="#fff" text-anchor="middle" font-family="Open Sans,sans-serif">$</text></svg></div>
    <div class="tool"><svg width="22" height="22" viewBox="0 0 22 22" fill="none" stroke="#fff" stroke-width="2.5"><path d="M2 7V2h5M15 2h5v5M20 15v5h-5M7 20H2v-5"/></svg></div>
    <div class="tool"><svg width="22" height="22" viewBox="0 0 22 22"><path d="M8 4l11-2v13" fill="none" stroke="#fff" stroke-width="2.5"/><path d="M8 4v13" stroke="#fff" stroke-width="2.5"/><circle cx="5.5" cy="17" r="3" fill="#fff"/><circle cx="16.5" cy="15" r="3" fill="#fff"/></svg></div>
    <div class="tool close"><svg width="22" height="22" viewBox="0 0 22 22"><path d="M4 4l14 14M18 4L4 18" stroke="#fff" stroke-width="3.5"/></svg></div>
  </div>

  <div class="gloss tab blue" style="left:228px"><span>Bacarat</span>
    <svg class="tab-icon" width="64" height="54" viewBox="0 0 64 54"><rect x="8" y="14" width="26" height="34" rx="3" fill="#fff" stroke="#333" transform="rotate(-18 21 31)"/><rect x="20" y="10" width="26" height="34" rx="3" fill="#fff" stroke="#333"/><rect x="32" y="12" width="26" height="34" rx="3" fill="#fff" stroke="#333" transform="rotate(16 45 29)"/></svg></div>
  <div class="gloss tab green" style="left:500px"><span>Super six</span>
    <svg class="tab-icon" width="64" height="54" viewBox="0 0 64 54"><rect x="10" y="10" width="24" height="32" rx="3" fill="#fff" stroke="#333" transform="rotate(-14 22 26)"/><rect x="24" y="8" width="24" height="32" rx="3" fill="#fff" stroke="#333"/><ellipse cx="46" cy="44" rx="14" ry="6" fill="#d8261e"/><text x="46" y="32" font-size="24" font-weight="700" fill="#e8b923" text-anchor="middle" font-family="Open Sans,sans-serif">6</text></svg></div>
  <div class="gloss tab green" style="left:772px"><span>Roulette</span>
    <svg class="tab-icon" width="64" height="54" viewBox="0 0 64 54"><circle cx="34" cy="28" r="24" fill="#7a1a10" stroke="#c9a24a" stroke-width="3"/><circle cx="34" cy="28" r="15" fill="none" stroke="#e0d6b0" stroke-width="5" stroke-dasharray="4 3"/><circle cx="34" cy="28" r="7" fill="#c9a24a"/></svg></div>
  <div class="gloss tab green" style="left:1045px"><span>Sic Bo</span>
    <svg class="tab-icon" width="64" height="54" viewBox="0 0 64 54"><rect x="12" y="14" width="36" height="26" rx="8" fill="#3d4a66"/><rect x="20" y="22" width="14" height="14" rx="3" fill="#e33"/><rect x="30" y="32" width="14" height="14" rx="3" fill="#d22"/><circle cx="27" cy="29" r="1.6" fill="#fff"/><circle cx="37" cy="39" r="1.6" fill="#fff"/></svg></div>

  <div class="abs side-panel profile"></div>
  <div class="abs avatar" role="img" aria-label="Player avatar"></div>
  <div class="abs player-name">Kai207</div>
  <div class="gloss profile-btn"><span class="icon-box"><svg width="14" height="16" viewBox="0 0 14 16"><path d="M1 1h8l4 4v10H1z" fill="#fff"/></svg></span><span class="lbl">Profile</span></div>

  <div class="abs side-panel menu"></div>
  <div class="gloss menu-btn" style="top:435px"><span class="icon-box" style="background:var(--blue)"><svg width="16" height="16" viewBox="0 0 16 16"><circle cx="3" cy="13" r="2" fill="#fff"/><path d="M2 7a7 7 0 0 1 7 7M2 2a12 12 0 0 1 12 12" fill="none" stroke="#fff" stroke-width="2"/></svg></span><span class="lbl">Announcements</span></div>
  <div class="gloss menu-btn" style="top:488px"><span class="icon-box" style="background:var(--blue)"><svg width="16" height="16" viewBox="0 0 16 16"><rect x="2" y="1" width="12" height="14" fill="#fff"/><rect x="7" y="3" width="2" height="7" fill="#1e5fc4"/><rect x="7" y="11" width="2" height="2" fill="#1e5fc4"/></svg></span><span class="lbl">Rules &amp; Regulation</span></div>
  <div class="gloss menu-btn" style="top:541px"><span class="icon-box" style="background:var(--blue)"><svg width="16" height="16" viewBox="0 0 16 16"><circle cx="9" cy="7" r="5" fill="none" stroke="#fff" stroke-width="2"/><path d="M5 11l-4 4" stroke="#fff" stroke-width="2.5"/></svg></span><span class="lbl">Quick tour</span></div>

  <div class="abs dealer-frame" style="left:240px;top:110px;width:302px;height:142px">
    <div class="dealer-inner">
      <div class="dealer-photo" role="img" aria-label="Dealer portrait" style="left:8px;top:8px;width:96px;height:96px"></div>
      <div class="score-grid" style="left:106px;top:10px;width:182px;height:92px"></div>
      <div class="dealer-bar" style="left:8px;top:110px;width:280px;height:22px;font-size:12px;padding-left:12px">Dealer Name<span class="deals">Deals 999</span></div>
    </div>
  </div>

  <div class="abs dealer-group"><div class="dealer-group-inner">
    <div class="abs dealer-frame" style="left:13px;top:13px;width:245px;height:103px"><div class="dealer-inner">
      <div class="dealer-photo" role="img" aria-label="Dealer portrait" style="left:6px;top:4px;width:74px;height:72px"></div>
      <div class="score-grid" style="left:82px;top:4px;width:146px;height:72px"></div>
      <div class="dealer-bar" style="left:4px;top:78px;width:229px;height:17px;padding-left:8px">Dealer Name<span class="deals">Deals 999</span></div></div></div>
    <div class="abs dealer-frame" style="left:270px;top:13px;width:245px;height:103px"><div class="dealer-inner">
      <div class="dealer-photo" role="img" aria-label="Dealer portrait" style="left:6px;top:4px;width:74px;height:72px"></div>
      <div class="score-grid" style="left:82px;top:4px;width:146px;height:72px"></div>
      <div class="dealer-bar" style="left:4px;top:78px;width:229px;height:17px;padding-left:8px">Dealer Name<span class="deals">Deals 999</span></div></div></div>
    <div class="abs dealer-frame" style="left:528px;top:13px;width:245px;height:103px"><div class="dealer-inner">
      <div class="dealer-photo" role="img" aria-label="Dealer portrait" style="left:6px;top:4px;width:74px;height:72px"></div>
      <div class="score-grid" style="left:82px;top:4px;width:146px;height:72px"></div>
      <div class="dealer-bar" style="left:4px;top:78px;width:229px;height:17px;padding-left:8px">Dealer Name<span class="deals">Deals 999</span></div></div></div>
  </div></div>

  <div class="abs filter-bar"></div>
  <div class="abs chip" style="left:246px;width:158px;justify-content:flex-start;padding-left:4px;gap:18px"><span class="icon-box" style="background:#fff;border-color:#999"><svg width="18" height="18" viewBox="0 0 18 18"><circle cx="9" cy="5" r="4" fill="#111"/><path d="M1 18c0-6 16-6 16 0z" fill="#111"/></svg></span>Multiplayer</div>
  <div class="abs chip search" style="left:410px;width:325px"></div>
  <div class="abs chip" style="left:757px;width:127px">Join any</div>
  <div class="abs chip" style="left:889px;width:48px;font-size:13px">A<svg width="12" height="10" viewBox="0 0 12 10"><path d="M0 5h8M5 1l4 4-4 4" fill="none" stroke="#111" stroke-width="2"/></svg>Z</div>
  <div class="abs chip" style="left:941px;width:48px;font-size:14px;font-weight:700;gap:2px">$<svg width="10" height="12" viewBox="0 0 10 12"><path d="M5 0v8M1 6l4 5 4-5" fill="none" stroke="#111" stroke-width="2.2"/></svg></div>
  <div class="abs chip" style="left:993px;width:50px;font-size:14px;font-weight:700;gap:2px">$<svg width="10" height="12" viewBox="0 0 10 12"><path d="M5 12V4M1 6l4-5 4 5" fill="none" stroke="#111" stroke-width="2.2"/></svg></div>
  <div class="abs chip" style="left:1051px;width:49px"><svg width="30" height="20" viewBox="0 0 30 20"><circle cx="8" cy="6" r="4" fill="#111"/><circle cx="22" cy="6" r="4" fill="#111"/><circle cx="15" cy="7" r="5" fill="#111"/><path d="M2 20c0-6 26-6 26 0z" fill="#111"/></svg></div>
  <div class="abs chip" style="left:1105px;width:51px;font-size:14px">⩽ 3</div>
  <div class="abs chip" style="left:1159px;width:49px;font-size:14px">&gt;3</div>
  <div class="abs chip" style="left:1212px;width:126px;font-size:15px;gap:10px">All Limits <svg width="14" height="9" viewBox="0 0 14 9"><path d="M0 0h14L7 9z" fill="#111"/></svg></div>

  <!-- table cards -->
  <div class="abs table-card" style="left:272px;top:345px">
    <div class="abs t-title">Baccarat A5-3C</div><div class="abs t-limit">Bet Limit</div>
    <div class="abs t-comm">Commission 0/7</div><div class="abs t-count">0/100</div>
    <div class="abs coin">JOIN</div>
    <svg class="abs felt" width="300" height="60"><use href="#felt"/></svg>
    <div class="abs seats">
      <div class="seat"><svg width="20" height="20"><use href="#person"/></svg></div><div class="seat"><svg width="20" height="20"><use href="#person"/></svg></div><div class="seat"><svg width="20" height="20"><use href="#person"/></svg></div><div class="seat"><svg width="20" height="20"><use href="#person"/></svg></div><div class="seat"><svg width="20" height="20"><use href="#person"/></svg></div>
      <div class="seat open"><svg width="22" height="16"><use href="#drop"/></svg></div><div class="seat open"><svg width="22" height="16"><use href="#drop"/></svg></div>
    </div>
  </div>

  <div class="abs table-card" style="left:625px;top:345px">
    <div class="abs t-title">Baccarat A5-3C</div><div class="abs t-limit">Bet Limit</div>
    <div class="abs t-comm">Commission 0/7</div><div class="abs t-count">0/100</div>
    <div class="abs coin">JOIN</div>
    <svg class="abs felt" width="300" height="60"><use href="#felt"/></svg>
    <div class="abs seats">
      <div class="seat"><svg width="20" height="20"><use href="#person"/></svg></div><div class="seat"><svg width="20" height="20"><use href="#person"/></svg></div><div class="seat"><svg width="20" height="20"><use href="#person"/></svg></div><div class="seat"><svg width="20" height="20"><use href="#person"/></svg></div><div class="seat"><svg width="20" height="20"><use href="#person"/></svg></div>
      <div class="seat open"><svg width="22" height="16"><use href="#drop"/></svg></div><div class="seat open"><svg width="22" height="16"><use href="#drop"/></svg></div>
    </div>
  </div>

  <div class="abs table-card" style="left:978px;top:345px">
    <div class="abs t-title">Baccarat A5-3C</div><div class="abs t-limit">Bet Limit</div>
    <div class="abs t-comm">Commission 0/7</div><div class="abs t-count">0/100</div>
    <div class="abs coin">JOIN</div>
    <svg class="abs felt" width="300" height="60"><use href="#felt"/></svg>
    <div class="abs seats">
      <div class="seat"><svg width="20" height="20"><use href="#person"/></svg></div><div class="seat"><svg width="20" height="20"><use href="#person"/></svg></div><div class="seat"><svg width="20" height="20"><use href="#person"/></svg></div><div class="seat"><svg width="20" height="20"><use href="#person"/></svg></div><div class="seat"><svg width="20" height="20"><use href="#person"/></svg></div>
      <div class="seat open"><svg width="22" height="16"><use href="#drop"/></svg></div><div class="seat open"><svg width="22" height="16"><use href="#drop"/></svg></div>
    </div>
  </div>

  <div class="abs table-card" style="left:272px;top:528px">
    <div class="abs t-title">Baccarat A5-3C</div><div class="abs t-limit">Bet Limit</div>
    <div class="abs t-comm">Commission 0/7</div><div class="abs t-count">0/100</div>
    <div class="abs coin">JOIN</div>
    <svg class="abs felt" width="300" height="60"><use href="#felt"/></svg>
    <div class="abs seats">
      <div class="seat"><svg width="20" height="20"><use href="#person"/></svg></div><div class="seat"><svg width="20" height="20"><use href="#person"/></svg></div><div class="seat"><svg width="20" height="20"><use href="#person"/></svg></div><div class="seat"><svg width="20" height="20"><use href="#person"/></svg></div><div class="seat"><svg width="20" height="20"><use href="#person"/></svg></div>
      <div class="seat open"><svg width="22" height="16"><use href="#drop"/></svg></div><div class="seat open"><svg width="22" height="16"><use href="#drop"/></svg></div>
    </div>
  </div>

  <div class="abs table-card" style="left:625px;top:528px">
    <div class="abs t-title">Baccarat A5-3C</div><div class="abs t-limit">Bet Limit</div>
    <div class="abs t-comm">Commission 0/7</div><div class="abs t-count">0/100</div>
    <div class="abs coin">JOIN</div>
    <svg class="abs felt" width="300" height="60"><use href="#felt"/></svg>
    <div class="abs seats">
      <div class="seat"><svg width="20" height="20"><use href="#person"/></svg></div><div class="seat"><svg width="20" height="20"><use href="#person"/></svg></div><div class="seat"><svg width="20" height="20"><use href="#person"/></svg></div><div class="seat"><svg width="20" height="20"><use href="#person"/></svg></div><div class="seat"><svg width="20" height="20"><use href="#person"/></svg></div>
      <div class="seat open"><svg width="22" height="16"><use href="#drop"/></svg></div><div class="seat open"><svg width="22" height="16"><use href="#drop"/></svg></div>
    </div>
  </div>

  <div class="abs table-card" style="left:981px;top:528px">
    <div class="abs t-title">Baccarat A5-3C</div><div class="abs t-limit">Bet Limit</div>
    <div class="abs t-comm">Commission 0/7</div><div class="abs t-count">0/100</div>
    <div class="abs coin">JOIN</div>
    <svg class="abs felt" width="300" height="60"><use href="#felt"/></svg>
    <div class="abs seats">
      <div class="seat"><svg width="20" height="20"><use href="#person"/></svg></div><div class="seat"><svg width="20" height="20"><use href="#person"/></svg></div><div class="seat"><svg width="20" height="20"><use href="#person"/></svg></div><div class="seat"><svg width="20" height="20"><use href="#person"/></svg></div><div class="seat"><svg width="20" height="20"><use href="#person"/></svg></div>
      <div class="seat open"><svg width="22" height="16"><use href="#drop"/></svg></div><div class="seat open"><svg width="22" height="16"><use href="#drop"/></svg></div>
    </div>
  </div>

  <div class="abs scroll-track"></div>
  <div class="abs scroll-thumb"></div>

  <div class="abs balance"><span class="balance-label">Balance</span><span class="currency">$ SGD ◀</span><span class="balance-value">999,999,999</span></div>
</div>
</body>
</html>
```